Business card design needed

Family General Practitioner/ Family Physician.
Logo is the logo of the Noble Guild of Family Healers Oceania
http://kpltw.varendo.example/ImageShelf/marks/pages/NGFHO%20mark_jpg.htm
Updates

Project Deadline Extended
Reason: Just a bit more time to make changes and the weekend for me to look at things closely and to choose. Thanks, Orin

Thanks for all the submissions. So many of them are really works of art. Not one of them are not good. The ones that I am eliminating are the ones that I think are not suitable for me personally only, and because if I don't, it makes it very difficult to decide as many of you are also sending me slight variations of a card. I have just decided to choose a second place card too. Can't thank you all enough. Good luck, Orin. P.S - Working today till 10 pm as the card says :-), so probably won't be able to give a feedback till late Saturday night or Sunday morning here in Sydney, Australia. 

Project Deadline Extended
Reason: Just added a second place to the budget and realised that Australia is ahead of the rest of the world in the time zone (only :-) - don't want to offend anyone or start a debate!! ) , so Monday deadline will mean it will be a weekend for the rest of the world. Just wanted to give everyone more time to submit their best, especially since I will be picking a second card too. Can't thank everyone enough for the submissions. P.S - Not keen on photos on the card.

Industry/Entity Type

Business

Contact Information for Business Card

Dr. Orin Halvey M.B.B.S., F.N.G.F.H.O
Family General Practitioner
Address, timings, phone and fax number on the back.

Requirements
Must have
• Timings
Mon 7 am - 7 pm
Tues 7 am - 12 pm
Wed 7 am - 10 pm
Thurs 7 am - 12 pm
Fri 7 am - 8 pm
Sat 8 am - 10 pm
Sun - Off

```html
<!DOCTYPE html>
<html lang="en">
<head>
<meta charset="utf-8">
<title>Dr. Orin Halvey – Business Card Options</title>
<link href="https://fonts.googleapis.com/css2?family=Cinzel:wght@400&family=Open+Sans:wght@400;700;800&family=Tinos:wght@400;700&display=swap" rel="stylesheet">
<style>
  :root {
    --page: #ebe8e3;
    --blue-deep: #24389a;
    --blue-mid: #2a4fb4;
    --blue-glow: #2aa6e4;
    --red: #e31c24;
    --red-deep: #c8161d;
    --gold: #f2b233;
    --orange: #f08a1c;
    --silver: #c9cdd6;
    --white: #ffffff;
    --label: #3a2a1c;
  }
  * { box-sizing: border-box; margin: 0; padding: 0; }
  html, body { width: 1200px; height: 739px; overflow: hidden; }
  body { background: var(--page); position: relative; font-family: "Open Sans", sans-serif; }

  .card {
    position: absolute; width: 526px; height: 300px; overflow: hidden;
    box-shadow: 0 2px 5px rgba(0,0,0,.25);
    color: var(--white);
  }
  .card--front { left: 37px; top: 24px;
    background: radial-gradient(ellipse 60% 70% at 45% 45%, var(--blue-mid), var(--blue-deep) 80%); }
  .card--opt1 { left: 620px; top: 27px; }
  .card--opt2 { left: 47px; top: 371px; }
  .card--opt3 { left: 616px; top: 379px; }

  /* front */
  .front-wave { position: absolute; inset: 0; }
  .doctor-name {
    position: absolute; top: 48px; width: 100%; text-align: center;
    font-family: "Cinzel", serif; font-size: 40px; letter-spacing: 1px;
  }
  .credentials {
    position: absolute; top: 98px; width: 100%; text-align: center;
    font-family: "Tinos", serif; font-size: 11px; letter-spacing: 1px;
  }
  .specialty {
    position: absolute; top: 142px; width: 100%; text-align: center;
    font-family: "Tinos", serif; font-size: 20px; letter-spacing: 2px;
  }
  .tagline {
    position: absolute; left: 123px; top: 256px;
    font-family: "Tinos", serif; font-weight: 700; font-size: 22px;
  }
  .guild-mark {
    position: absolute; left: 424px; top: 212px; width: 90px;
    display: flex; flex-direction: column; align-items: center; gap: 3px;
    font-family: "Tinos", serif; font-size: 9px; line-height: 1.15; text-align: center;
  }
  .guild-mark .dot { width: 22px; height: 22px; border-radius: 50%; background: var(--gold); }

  /* backs */
  .back-top {
    position: absolute; left: 0; top: 0; width: 100%; height: 218px;
    background: radial-gradient(ellipse 45% 60% at 52% 62%, var(--blue-glow), var(--blue-mid) 55%, var(--blue-deep) 95%);
  }
  .back-rule { position: absolute; left: 0; top: 218px; width: 100%; height: 2px; background: var(--gold); opacity: .8; }
  .back-bottom {
    position: absolute; left: 0; top: 220px; width: 100%; height: 80px;
    background: linear-gradient(var(--red), var(--red-deep));
    font-family: "Tinos", serif; font-size: 15px; text-align: center; line-height: 19px; padding-top: 8px;
  }
  .contact-line { margin-top: 7px; }
  .contact-line .sep { display: inline-block; width: 1px; height: 17px; background: var(--white); vertical-align: -3px; margin: 0 7px; }

  .guild-watermark {
    position: absolute; left: 285px; top: 30px; width: 190px; height: 170px;
    display: flex; flex-direction: column; align-items: center; justify-content: center; gap: 8px;
    color: rgba(255,255,255,.12); font-family: "Open Sans", sans-serif; font-size: 15px; text-align: center; line-height: 1.2;
  }
  .guild-watermark .dot { width: 60px; height: 60px; border-radius: 50%; background: rgba(255,255,255,.08); }

  .hours-title { position: absolute; font-size: 19px; font-weight: 400; }
  .hours { position: absolute; list-style: none; }
  .hours li { height: 23px; line-height: 23px; font-size: 16px; white-space: pre; }
  .hours b { font-weight: 700; }

  .card--opt1 .hours-title { left: 38px; top: 16px; }
  .card--opt1 .hours { left: 38px; top: 45px; }
  .card--opt1 .hours li { font-weight: 800; text-transform: uppercase; font-size: 15px; }

  .card--opt2 .hours-title { left: 50px; top: 5px; font-size: 20px; letter-spacing: .5px; }
  .card--opt2 .hours { left: 31px; top: 38px; }
  .card--opt2 .day { display: inline-block; width: 109px; }

  .card--opt3 .hours-title { left: 33px; top: 14px; }
  .card--opt3 .hours { left: 33px; top: 42px; }

  .option-label {
    position: absolute; font-weight: 800; font-size: 20px; color: var(--label);
  }
</style>
</head>
<body>

  <section class="card card--front" aria-label="Card front">
    <svg class="front-wave" viewBox="0 0 526 300" width="526" height="300" aria-hidden="true">
      <path d="M0,150 C60,190 140,215 250,215 C350,215 440,185 526,178" fill="none" stroke="var(--orange)" stroke-width="7"/>
      <path d="M0,168 C80,210 170,232 270,226 C370,220 450,196 526,190" fill="none" stroke="var(--gold)" stroke-width="4"/>
      <path d="M0,186 C90,226 190,246 290,236 C390,226 460,204 526,198" fill="none" stroke="var(--silver)" stroke-width="9"/>
      <path d="M0,196 C90,236 190,254 290,244 C390,234 460,212 526,206" fill="none" stroke="var(--blue-mid)" stroke-width="4"/>
      <path d="M0,204 C90,244 190,262 290,252 C390,242 460,220 526,214 L526,300 L0,300 Z" fill="var(--red)"/>
    </svg>
    <h1 class="doctor-name">Dr. Orin Halvey</h1>
    <p class="credentials">M.B.B.S., F.N.G.F.H.O</p>
    <p class="specialty">Family General Practitioner</p>
    <p class="tagline">Caring about your health</p>
    <div class="guild-mark">
      <span class="dot"></span>
      <span>Noble Guild of Family Healers Oceania</span>
    </div>
  </section>

  <section class="card card--opt1" aria-label="Card back, option 1">
    <div class="back-top"></div>
    <div class="guild-watermark"><span class="dot"></span><span>Noble Guild of Family Healers Oceania</span></div>
    <h2 class="hours-title">Working Hours</h2>
    <ul class="hours">
      <li>Monday   7 AM  - 7 PM</li>
      <li>Tuesday  7 AM - 12 PM</li>
      <li>Wednesday  7 AM - 10 PM</li>
      <li>Thursday  7 AM - 12 PM</li>
      <li>Friday    7 AM   - 8 PM</li>
      <li>Saturday  8 AM - 10 PM</li>
      <li>Sunday - Off</li>
    </ul>
    <div class="back-rule"></div>
    <div class="back-bottom">
      <p>Upper Level, Linden Court, Harbourgate Shopping Centre<br>Ferncliff, NSW 2199</p>
      <p class="contact-line">P: 02 5550 1400<span class="sep"></span>F: 02 5550 1433</p>
    </div>
  </section>

  <section class="card card--opt2" aria-label="Card back, option 2">
    <div class="back-top"></div>
    <div class="guild-watermark"><span class="dot"></span><span>Noble Guild of Family Healers Oceania</span></div>
    <h2 class="hours-title">Working Hours</h2>
    <ul class="hours">
      <li><span class="day">Monday</span><b>7 AM   - 7 PM</b></li>
      <li><span class="day">Tuesday</span><b>7 AM - 12 PM</b></li>
      <li><span class="day">Wednesday</span><b>7 AM - 10 PM</b></li>
      <li><span class="day">Thursday</span><b>7 AM - 12 PM</b></li>
      <li><span class="day">Friday</span><b>7 AM   - 8 PM</b></li>
      <li><span class="day">Saturday</span><b>8 AM - 10 PM</b></li>
      <li><span class="day">Sunday</span><b>OFF</b></li>
    </ul>
    <div class="back-rule"></div>
    <div class="back-bottom">
      <p>Upper Level, Linden Court, Harbourgate Shopping Centre<br>Ferncliff, NSW 2199</p>
      <p class="contact-line">P: 02 5550 1400<span class="sep"></span>F: 02 5550 1433</p>
    </div>
  </section>

  <section class="card card--opt3" aria-label="Card back, option 3">
    <div class="back-top"></div>
    <div class="guild-watermark"><span class="dot"></span><span>Noble Guild of Family Healers Oceania</span></div>
    <h2 class="hours-title">Working Hours</h2>
    <ul class="hours">
      <li>Monday  <b>7 AM   - 7 PM</b></li>
      <li>Tuesday  <b>7 AM - 12 PM</b></li>
      <li>Wednesday  <b>7 AM - 10 PM</b></li>
      <li>Thursday  <b>7 AM - 12 PM</b></li>
      <li>Friday    <b>7 AM   - 8 PM</b></li>
      <li>Saturday  <b>8 AM - 10 PM</b></li>
      <li>Sunday - <b>OFF</b></li>
    </ul>
    <div class="back-rule"></div>
    <div class="back-bottom">
      <p>Upper Level, Linden Court, Harbourgate Shopping Centre<br>Ferncliff, NSW 2199</p>
      <p class="contact-line">P: 02 5550 1400<span class="sep"></span>F: 02 5550 1433</p>
    </div>
  </section>

  <p class="option-label" style="left:830px; top:340px;">Option# 1</p>
  <p class="option-label" style="left:257px; top:681px;">Option# 2</p>
  <p class="option-label" style="left:826px; top:689px;">Option# 3</p>

</body>
</html>
```